I need to create a product box

I need a designer for a candle-making kit. Attached please find the die-cut and some of the elements I will like to include in the box. Also, there is a sample box. I want the designer to know this is an ecofriendly product but the packaging needs to be classy, unisex and eye-catching.

file:///C:/Users/mauro/Downloads/Untitled%20design.svg

Colors
0054AA
0677BA
7BADD7
CADEEF
E8F1F8
0094D4
00A9DD
6FCCEA
C7EBF8
E9F6FB
00AB8E
00BBA5
67D7C9
C6EFE9
E9F9F6
FFF300
FFF600
FEFA6F
FFFEC7
FFFEE8
FFC000
F8CF3A
FAE287
FDF2CF
FEFAEE
F0912C
F2A743
F7CA91
FBE8D2
FDF5EE
A7469A
B969AE
D3A5CF
EDDBEB
F8F0F9

```html
<!DOCTYPE html>
<html lang="en">
<head>
<meta charset="utf-8">
<title>Emberloom – Candle Making Kit Box Dieline</title>
<link href="https://fonts.googleapis.com/css2?family=Allura&family=Alegreya:wght@400;500&family=Open+Sans:wght@400;600&family=Roboto+Condensed:wght@400;700&family=Montserrat:wght@300;500&display=swap" rel="stylesheet">
<style>
  :root {
    --bg: #dcc5df;
    --board: #f1e8e9;
    --cutline: #b9a6b9;
    --sage: #627a5e;
    --sage-soft: #c9d3c5;
    --sage-pale: #e1e6dc;
    --lilac-text: #9d84ad;
    --lilac-frame: #d9cfe2;
    --ink: #4f4a4f;
    --white: #ffffff;
    --petal-blue: #9fa8db;
    --petal-lilac: #b4a6d8;
    --petal-pink: #e9a9b8;
    --petal-rose: #f0cbd6;
    --petal-yellow: #ecdc8e;
    --petal-green: #b9dca6;
    --leaf: #a9cbb0;
  }
  * { margin: 0; padding: 0; box-sizing: border-box; }
  html, body { width: 1200px; height: 1200px; overflow: hidden; background: var(--bg); }
  .canvas { position: relative; width: 1200px; height: 1200px; }
  .dieline, .art-layer { position: absolute; left: 0; top: 0; }
  .layer { position: absolute; }
  .upside-down { transform: rotate(180deg); }

  .quote {
    font-family: "Allura", cursive;
    color: var(--sage);
    font-size: 19px;
    text-align: center;
    white-space: nowrap;
    line-height: 25px;
  }

  .lid-flap { left: 425px; top: 117px; width: 350px; height: 178px; }
  .lid-flap .heart { position: absolute; left: 166px; top: 36px; }
  .lid-flap .quote { position: absolute; left: 0; right: 0; top: 72px; }

  .inner-base { left: 425px; top: 295px; width: 350px; height: 235px; }
  .framed-box { position: absolute; border: 3px solid var(--lilac-frame); top: 35px; height: 165px; }
  .warnings { left: 19px; width: 193px; padding: 8px 10px; font-family: "Roboto Condensed", sans-serif; color: var(--ink); }
  .warnings h4 { font-size: 5.6px; font-weight: 700; letter-spacing: .2px; margin-top: 4px; }
  .warnings h4::before { content: "⚠ "; font-weight: 400; }
  .warnings p { font-size: 4.6px; line-height: 5.8px; text-align: justify; }
  .kit-list { left: 220px; width: 112px; padding: 9px 8px; font-family: "Open Sans", sans-serif; color: var(--lilac-text); }
  .kit-list h3 { font-weight: 400; font-size: 10.5px; margin-bottom: 6px; letter-spacing: .3px; }
  .kit-list ol { list-style: none; font-size: 5.4px; line-height: 8.5px; }
  .kit-list li span { display: inline-block; width: 11px; }

  .floor-panel { left: 425px; top: 530px; width: 350px; height: 178px; }
  .floor-panel .quote { position: absolute; left: 0; right: 0; top: 76px; }

  .side-left { left: 245px; top: 295px; width: 180px; height: 235px; }
  .paraben-free {
    position: absolute; left: 104px; top: 28px;
    transform: rotate(90deg); transform-origin: left top;
    font-family: "Montserrat", sans-serif; color: var(--white);
    line-height: 1; white-space: nowrap;
  }
  .paraben-free .small { font-size: 6.5px; font-weight: 500; letter-spacing: .6px; display: block; }
  .paraben-free .big { font-size: 12px; font-weight: 300; letter-spacing: .6px; display: block; margin-top: 1px; }
  .site-url {
    position: absolute; left: 34px; top: 72px;
    transform: rotate(90deg); transform-origin: left top;
    font-family: "Open Sans", sans-serif; font-weight: 600; font-size: 8px;
    color: var(--white); letter-spacing: .2px; white-space: nowrap;
  }
  .trust-badge { position: absolute; left: 65px; }

  .brand-lockup { position: absolute; text-align: center; color: var(--sage); }
  .brand-name { font-family: "Alegreya", serif; font-weight: 500; font-size: 25px; line-height: 1; display: block; letter-spacing: .3px; }
  .brand-tag { font-family: "Alegreya", serif; font-size: 4.6px; letter-spacing: 1.3px; display: block; margin-top: 6px; }
</style>
</head>
<body>
<div class="canvas">

  <svg class="dieline" width="1200" height="1200" viewBox="0 0 1200 1200" aria-hidden="true">
    <defs>
      <linearGradient id="sketch-sage" x1="0" y1="0" x2="0" y2="1">
        <stop offset="0" stop-color="#dfe5da"/>
        <stop offset="1" stop-color="#c8d2c3"/>
      </linearGradient>
    </defs>
    <g fill="var(--board)" stroke="var(--cutline)" stroke-width="0.8">
      <rect x="321" y="117" width="558" height="178"/>
      <rect x="66" y="295" width="1067" height="235"/>
      <rect x="321" y="530" width="558" height="178"/>
      <path d="M425,708 H334 Q259,708 259,783 V867 Q259,942 334,942 H425 Z"/>
      <path d="M775,708 H866 Q941,708 941,783 V867 Q941,942 866,942 H775 Z"/>
      <rect x="425" y="708" width="350" height="234"/>
      <path d="M425,942 L352,949 Q321,953 321,983 V1052 Q321,1068 338,1077 L425,1121 H775 L862,1077 Q879,1068 879,1052 V983 Q879,953 848,949 L775,942 Z"/>
    </g>
    <g fill="var(--sage)">
      <rect x="245" y="295" width="180" height="235"/>
      <rect x="775" y="295" width="180" height="235"/>
      <rect x="57" y="388" width="9" height="56"/>
      <rect x="425" y="388" width="9" height="56"/>
      <rect x="766" y="388" width="9" height="56"/>
      <rect x="1133" y="388" width="10" height="56"/>
    </g>
    <g stroke="var(--cutline)" stroke-width="0.8">
      <line x1="425" y1="117" x2="425" y2="295"/>
      <line x1="775" y1="117" x2="775" y2="295"/>
      <line x1="425" y1="530" x2="425" y2="708"/>
      <line x1="775" y1="530" x2="775" y2="708"/>
      <line x1="425" y1="942" x2="775" y2="942" stroke="#a9c3a3"/>
    </g>
  </svg>

  <!-- inner base faint flowers -->
  <svg class="art-layer" width="1200" height="1200" viewBox="0 0 1200 1200" role="img" aria-label="Faint line-drawn flowers on the inner base">
    <g fill="var(--lilac-frame)" opacity=".6">
      <circle cx="456" cy="314" r="12"/>
      <circle cx="680" cy="314" r="12"/>
      <circle cx="437" cy="513" r="9"/>
      <circle cx="638" cy="512" r="11"/>
    </g>
  </svg>

  <!-- left side panel flowers -->
  <svg class="art-layer" width="1200" height="1200" viewBox="0 0 1200 1200" role="img" aria-label="Line-drawn pastel flowers and a leaf on the left side panel">
    <ellipse cx="290" cy="325" rx="18" ry="10" transform="rotate(-35 290 325)" fill="var(--leaf)" opacity=".55"/>
    <circle cx="271" cy="327" r="17" fill="var(--petal-rose)" opacity=".7"/>
    <circle cx="252" cy="422" r="9" fill="var(--petal-lilac)" opacity=".6"/>
    <circle cx="273" cy="484" r="18" fill="var(--petal-blue)" opacity=".75"/>
    <path d="M356,530 A20,20 0 0 1 396,530 Z" fill="var(--petal-yellow)" opacity=".85"/>
    <circle cx="376" cy="512" r="20" fill="var(--petal-yellow)" opacity=".85"/>
  </svg>

  <!-- right side panel flowers -->
  <svg class="art-layer" width="1200" height="1200" viewBox="0 0 1200 1200" role="img" aria-label="Scattered line-drawn pastel flowers and leaves on the right side panel">
    <ellipse cx="880" cy="410" rx="32" ry="12" transform="rotate(20 880 410)" fill="var(--leaf)" opacity=".55"/>
    <ellipse cx="830" cy="505" rx="20" ry="9" transform="rotate(60 830 505)" fill="var(--leaf)" opacity=".55"/>
    <circle cx="801" cy="346" r="14" fill="var(--petal-green)" opacity=".75"/>
    <circle cx="815" cy="329" r="18" fill="var(--petal-blue)" opacity=".8"/>
    <circle cx="902" cy="348" r="17" fill="var(--petal-pink)" opacity=".85"/>
    <circle cx="810" cy="401" r="19" fill="var(--petal-lilac)" opacity=".8"/>
    <circle cx="919" cy="428" r="20" fill="var(--petal-yellow)" opacity=".85"/>
    <circle cx="808" cy="497" r="22" fill="var(--petal-rose)" opacity=".7"/>
    <circle cx="922" cy="494" r="20" fill="var(--petal-blue)" opacity=".7"/>
  </svg>

  <!-- front panel illustration -->
  <svg class="art-layer" width="1200" height="1200" viewBox="0 0 1200 1200" role="img" aria-label="Sketched bamboo, orchid, zen stones and a lit candle with pastel flowers on the front panel">
    <rect x="534" y="710" width="112" height="210" rx="22" fill="url(#sketch-sage)" opacity=".85"/>
    <ellipse cx="484" cy="739" rx="30" ry="12" transform="rotate(-45 484 739)" fill="var(--leaf)" opacity=".45"/>
    <ellipse cx="746" cy="884" rx="30" ry="10" transform="rotate(15 746 884)" fill="var(--leaf)" opacity=".45"/>
    <circle cx="460" cy="762" r="22" fill="var(--petal-rose)" opacity=".6"/>
    <circle cx="455" cy="826" r="23" fill="var(--petal-lilac)" opacity=".7"/>
    <circle cx="447" cy="888" r="22" fill="var(--petal-blue)" opacity=".7"/>
    <circle cx="476" cy="894" r="15" fill="var(--petal-blue)" opacity=".7"/>
    <circle cx="512" cy="857" r="23" fill="var(--petal-yellow)" opacity=".6"/>
    <circle cx="643" cy="832" r="22" fill="var(--petal-green)" opacity=".7"/>
    <circle cx="646" cy="884" r="22" fill="var(--petal-lilac)" opacity=".5"/>
    <circle cx="689" cy="861" r="22" fill="var(--petal-green)" opacity=".6"/>
    <circle cx="727" cy="845" r="22" fill="var(--petal-pink)" opacity=".7"/>
    <circle cx="751" cy="860" r="20" fill="var(--petal-lilac)" opacity=".85"/>
  </svg>

  <!-- dust flap illustration -->
  <svg class="art-layer" width="1200" height="1200" viewBox="0 0 1200 1200" role="img" aria-label="Sketched orchid, stones and candle with pastel flowers on the dust flap">
    <path d="M425,944 H535 Q553,944 553,962 V1080 Q553,1100 533,1100 H425 Z" fill="url(#sketch-sage)" opacity=".85"/>
    <circle cx="671" cy="994" r="18" fill="var(--petal-rose)" opacity=".6"/>
    <circle cx="723" cy="969" r="18" fill="var(--petal-pink)" opacity=".7"/>
    <circle cx="751" cy="984" r="16" fill="var(--petal-yellow)" opacity=".7"/>
    <circle cx="714" cy="1009" r="15" fill="var(--petal-lilac)" opacity=".55"/>
    <circle cx="686" cy="1028" r="15" fill="var(--petal-green)" opacity=".7"/>
    <circle cx="723" cy="1043" r="18" fill="var(--petal-lilac)" opacity=".45"/>
    <circle cx="754" cy="1037" r="17" fill="var(--petal-blue)" opacity=".7"/>
  </svg>

  <div class="layer lid-flap upside-down">
    <svg class="heart" width="18" height="16" viewBox="0 0 18 16" aria-hidden="true">
      <path d="M9 15 C4 11 0 8 0 4.5 C0 2 2 0 4.5 0 C6.5 0 8 1.3 9 3 C10 1.3 11.5 0 13.5 0 C16 0 18 2 18 4.5 C18 8 14 11 9 15 Z" fill="var(--sage)"/>
    </svg>
    <p class="quote">When everything seemed dark, I lit up a candle<br>Hope this kit can help you light up your path to happiness</p>
  </div>

  <div class="layer inner-base upside-down">
    <div class="framed-box warnings">
      <h4>WARNING:</h4>
      <p>Burn within sight and away from drafts. Keep away from children and pets. Place on a heat-resistant plate and trim wick before each use.</p>
      <h4>WARNING:</h4>
      <p>Do not microwave. Do not exceed wax temperature listed in the instructions. If wax catches fire, smother with a lid. Never use water.</p>
      <h4>AVERTISSEMENT:</h4>
      <p>Faire brûler à portée de vue, loin des courants d'air. Garder hors de portée des enfants et des animaux. Couper la mèche avant chaque utilisation.</p>
      <h4>AVERTISSEMENT:</h4>
      <p>Ne pas chauffer au micro-ondes. Ne pas dépasser la température indiquée. Si la cire prend feu, étouffer avec un couvercle.</p>
    </div>
    <div class="framed-box kit-list">
      <h3>DYI Candle Set</h3>
      <ol>
        <li><span>1.</span>7 Bags of soy wax (8 oz each)</li>
        <li><span>2.</span>4 Glass Jars (7 cm)</li>
        <li><span>3.</span>3 Black tin cans (8 oz each)</li>
        <li><span>4.</span>20 Decorative labels</li>
        <li><span>5.</span>3 Bags of dry flowers</li>
        <li><span>6.</span>2 Gift labels</li>
        <li><span>7.</span>3 Centering devices</li>
        <li><span>8.</span>7 Fragrance oil (10ml each)</li>
        <li><span>9.</span>1 Digital thermometer</li>
        <li><span>10.</span>1 mixing spoon</li>
        <li><span>11.</span>Candle wick</li>
        <li><span>12.</span>10 Glue dots</li>
        <li><span>13.</span>10 Color dye</li>
        <li><span>14.</span>1 Melting pot</li>
      </ol>
    </div>
  </div>

  <div class="layer floor-panel upside-down">
    <p class="quote">When everything seemed dark, I lit up a candle</p>
  </div>

  <div class="layer side-left">
    <div class="paraben-free"><span class="small">PARABEN</span><span class="big">FREE</span></div>
    <div class="site-url">www.emberloom.com</div>
    <svg class="trust-badge" style="top:68px" width="40" height="44" viewBox="0 0 40 44" role="img" aria-label="Non-toxic badge">
      <polygon points="20,1 39,11 39,33 20,43 1,33 1,11" fill="var(--white)"/>
    </svg>
    <svg class="trust-badge" style="top:113px" width="40" height="40" viewBox="0 0 40 40" role="img" aria-label="Guarantee badge">
      <circle cx="20" cy="20" r="18.5" fill="none" stroke="var(--white)" stroke-width="2"/>
      <circle cx="20" cy="20" r="14" fill="var(--white)"/>
    </svg>
    <svg class="trust-badge" style="top:161px" width="40" height="40" viewBox="0 0 40 40" role="img" aria-label="Premium quality badge">
      <circle cx="20" cy="20" r="19" fill="var(--white)"/>
    </svg>
  </div>

  <div class="brand-lockup" style="left:622px;top:768px;width:126px;">
    <span class="brand-name">Emberloom</span>
    <span class="brand-tag">LUXURY CANDLE MAKING KIT</span>
  </div>
  <div class="brand-lockup" style="left:537px;top:1035px;width:126px;">
    <span class="brand-name">Emberloom</span>
    <span class="brand-tag">LUXURY CANDLE MAKING KIT</span>
  </div>

</div>
</body>
</html>
```